Merrow Trade finance web design

We are a newly established business which provides invoice finance to Small Businesses in England and Wales.
Our approach is very much a funder where the small business owner can talk to the decision maker. We will guarantee on receipt of information, a decision within 24 hours.
We are not a bank so the look of the website need to be friendly but professional.
Have two types of people we are trying to attract to the website: 1) partners who are small business owners and 2) introducers who is accountants and commercial brokers who introduce us to the small businesses.
Currently no website, although domain has been reserved.
The design should be:
Professional
“Clean” Look
Designed to convey Trust and Authority.
Appeal to the small business owner.
Must incorporate:
Logo (attached)
Front page:Top tabs to other pages 1) About us 2) Services 3) Introducers 4) Contact us
Need picture and logo on page.
1) About us page- Room for talk about the company, the people and our critera.
2) Services page- We need for what invoice finance is, and 5 boxes for different services we will provide. (link on page to contact us)
3) Introducers page- We need a part for why become an introducer? Who we can help? Why we are different? (link on page to contact us)
4) Contact us page- Office address, email, tel and if possible a map and a contact me part which will email direct to us.
Text will be provided for the design, if we can see the setup of the website we will provide a part for each of the pages to support.
Styles we think convey the correct image:
www.dornelcapital.example
www.plivanlend.example
www.quorbacredit.example
Target Market(s)
Small business owners
Industry/Entity Type
Finance
Number of Pages Required
5+ page
Look and feel

```html
<!DOCTYPE html>
<html lang="en">
<head>
<meta charset="utf-8">
<title>Merrow Trade Finance</title>
<link rel="stylesheet" href="https://fonts.googleapis.com/css2?family=Ubuntu:wght@400;500;700&family=Roboto:wght@400;500;700&display=swap">
<style>
:root{
  --red:#b3141d;
  --red-dark:#8e0c12;
  --ink:#222222;
  --body:#555555;
  --grey-band:#ebebeb;
  --line:#dddddd;
  --white:#ffffff;
}
*{box-sizing:border-box;margin:0;padding:0}
html,body{width:1200px;height:3000px;overflow:hidden;background:var(--white)}
body{font-family:"Roboto",Arial,sans-serif;color:var(--body);position:relative}
.page{position:relative;width:1200px;height:3000px;overflow:hidden}
.abs{position:absolute}

/* hero */
.hero{left:0;top:0;width:1200px;height:626px;background:linear-gradient(180deg,#3d3f44 0%,#2a2c30 55%,#3a3530 100%)}
.brand{font-family:"Ubuntu",sans-serif;font-weight:700;color:var(--white);white-space:nowrap}
.brand-header{left:100px;top:30px;font-size:26px;line-height:40px}
.main-nav{right:100px;top:38px;display:flex}
.main-nav a{font-family:"Roboto",sans-serif;font-weight:500;color:var(--white);text-decoration:none;font-size:17px;margin-left:46px}
.nav-rule{left:100px;top:100px;width:1000px;height:1px;background:rgba(255,255,255,.55)}
.hero-title{left:0;top:174px;width:1200px;text-align:center;font-family:"Ubuntu",sans-serif;font-weight:500;color:var(--white);font-size:56px;line-height:64px}
.hero-sub{left:265px;top:262px;width:670px;text-align:center;color:var(--white);font-size:16.5px;line-height:29px;font-weight:500}
.signup-box{left:136px;top:372px;width:928px;height:90px;border:1px solid rgba(255,255,255,.8)}
.field{top:396px;height:44px;background:var(--white);border-radius:3px;font-size:14px;color:#333;padding:13px 10px}
.btn-red{background:var(--red);color:var(--white);font-family:"Roboto",sans-serif;font-weight:500;text-align:center;border-radius:2px}
.signup-btn{left:864px;top:396px;width:178px;height:44px;line-height:42px;font-size:15px;border:1px solid rgba(255,255,255,.6)}
.dots{left:550px;top:580px;display:flex;gap:6px}
.dots span{width:14px;height:14px;border-radius:50%;border:2px solid var(--white)}
.dots span.on{background:var(--red)}

/* about */
.section-title{font-family:"Ubuntu",sans-serif;font-weight:500;color:var(--ink);font-size:28px;line-height:36px}
.section-title em{font-style:normal;color:var(--red)}
.about-title{left:100px;top:670px}
.about-rule{left:100px;top:712px;width:288px;height:2px;background:var(--red)}
.copy{font-size:13px;line-height:23px;color:var(--body)}
.about-copy{left:100px;top:730px;width:560px}
.about-copy p{margin-bottom:12px}
.read-more{width:104px;height:46px;line-height:46px;font-size:14.5px}
.about-more{left:100px;top:908px}
.about-screen{left:710px;top:672px;width:390px;height:286px;background:linear-gradient(160deg,#d9d9d9,#bfbfbf);border-radius:4px}

/* services */
.services{left:0;top:1010px;width:1200px;height:500px;background:var(--grey-band)}
.services-title{left:0;top:1042px;width:1200px;text-align:center}
.services-rule{left:550px;top:1090px;width:100px;height:2px;background:var(--red)}
.card{top:1134px;width:304px;height:326px;background:var(--white);border-bottom:4px solid var(--red);text-align:center;box-shadow:0 1px 3px rgba(0,0,0,.08)}
.card svg{position:absolute;left:110px;top:28px}
.card-title{position:absolute;left:0;top:128px;width:100%;font-family:"Ubuntu",sans-serif;font-weight:500;font-size:19px;color:var(--ink);letter-spacing:.3px}
.card-text{position:absolute;left:26px;top:168px;width:252px;font-size:13.5px;line-height:22px;color:var(--body)}
.card .read-more{position:absolute;left:102px;top:252px;width:100px;height:42px;line-height:42px;font-size:13.5px}
.card.featured{background:var(--red);border-bottom-color:var(--red-dark)}
.card.featured .card-title,.card.featured .card-text{color:var(--white)}
.card.featured .read-more{background:transparent;border:1px solid var(--white);line-height:40px}

/* features */
.feature-img-one{left:100px;top:1548px;width:390px;height:250px;background:linear-gradient(135deg,#e9eef3,#c9d2dc);border-radius:4px}
.feature-head{font-family:"Ubuntu",sans-serif;font-weight:500;color:var(--red);font-size:22px;line-height:32px}
.feature-one-head{left:502px;top:1582px;width:600px}
.feature-one-copy{left:502px;top:1654px;width:598px}
.feature-two-head{left:100px;top:1864px}
.feature-two-copy{left:100px;top:1910px;width:570px}
.checks{left:100px;top:2004px;list-style:none}
.checks li{display:flex;align-items:center;gap:14px;height:36px;font-size:15px;font-weight:500;color:#333}
.feature-img-two{left:700px;top:1860px;width:400px;height:300px;background:linear-gradient(150deg,#eef1f5,#c7d3e3);border-radius:4px}

/* cta */
.cta{left:0;top:2190px;width:1200px;height:258px;background:linear-gradient(180deg,#2f2622,#3d322c 60%,#2a2320)}
.cta-title{left:0;top:2254px;width:1200px;text-align:center;font-family:"Ubuntu",sans-serif;font-weight:500;color:var(--white);font-size:30px;letter-spacing:.4px}
.cta-btn{left:508px;top:2332px;width:184px;height:48px;line-height:46px;border:1px solid var(--white);color:var(--white);text-align:center;font-size:16px;font-weight:500}

/* partners */
.partners{left:0;top:2448px;width:1200px;height:156px;background:#ececec}
.partner{top:2478px;width:132px;height:86px;background:var(--white);border:1px solid var(--line);border-radius:4px}
.partner i{position:absolute;left:34px;top:33px;width:64px;height:20px;background:#cfcfcf;border-radius:3px}

/* footer */
.footer{left:0;top:2604px;width:1200px;height:336px;background:linear-gradient(180deg,#c01b23,#b0141c)}
.brand-footer{left:100px;top:2710px;width:232px;text-align:center;font-size:24px;line-height:40px}
.social{left:100px;top:2792px;display:flex;gap:8px}
.social span{width:40px;height:40px;border-radius:50%;border:2px solid var(--white);display:flex;align-items:center;justify-content:center}
.social span::after{content:"";width:10px;height:10px;border-radius:50%;background:var(--white)}
.foot-title{font-family:"Ubuntu",sans-serif;font-weight:500;color:var(--white);font-size:17px;letter-spacing:.3px}
.foot-rule{height:1px;width:110px;background:rgba(255,255,255,.6)}
.quick-links{left:376px;top:2702px;list-style:none}
.quick-links li{color:var(--white);font-size:14.5px;height:32px}
.contact-list{left:526px;top:2696px;width:270px}
.contact-row{display:flex;gap:16px;margin-bottom:14px;color:var(--white);font-size:14px;line-height:20px}
.contact-row b{font-weight:700}
.contact-row .ic{flex:none;width:36px;height:36px;border-radius:50%;border:1px solid var(--white);display:flex;align-items:center;justify-content:center}
.foot-field{border:1px solid rgba(255,255,255,.8);border-radius:3px;color:var(--white);font-size:13px;padding:10px 8px}
.send-btn{left:812px;top:2822px;width:120px;height:38px;line-height:36px;border:1px solid var(--white);color:var(--white);font-size:13px;text-align:center;font-weight:500}
.bottom-bar{left:0;top:2940px;width:1200px;height:60px;background:var(--red-dark);text-align:center;line-height:60px;color:var(--white);font-size:14.5px}
</style>
</head>
<body>
<div class="page">

  <div class="abs hero" role="img" aria-label="Photo of a smiling business team giving thumbs up, darkened"></div>
  <div class="abs brand brand-header">Merrow Trade Finance</div>
  <nav class="abs main-nav">
    <a href="#">Home</a><a href="#">About Us</a><a href="#">Services</a><a href="#">Introducers</a><a href="#">Contact us</a>
  </nav>
  <div class="abs nav-rule"></div>
  <h1 class="abs hero-title">Welcome To Merrow</h1>
  <p class="abs hero-sub">We are a new business which provides invoice finance to Small Businesses in England and Wales.</p>
  <div class="abs signup-box"></div>
  <div class="abs field" style="left:158px;width:222px">Name</div>
  <div class="abs field" style="left:394px;width:222px">New Password</div>
  <div class="abs field" style="left:630px;width:222px">Industry</div>
  <div class="abs btn-red signup-btn">GET STARTED</div>
  <div class="abs dots"><span class="on"></span><span></span><span></span><span></span><span></span></div>

  <h2 class="abs section-title about-title">ABOUT <em>MERROW TRADE FINANCE</em></h2>
  <div class="abs about-rule"></div>
  <div class="abs copy about-copy">
    <p>Nemo enim ipsam voluptatem quia voluptas sit aspernatur aut odit aut fugit, sed quia consequuntur magni dolores eos qui ratione voluptatem sequi nesciunt. Neque porro quisquam est, qui dolorem ipsum quia dolor sit amet, consectetur, adipisci velit, sed quia non numquam</p>
    <p>Sed ut perspiciatis unde omnis iste natus error sit voluptatem accusantium doloremque laudantium, totam rem aperiam, eaque ipsa quae ab illo inventore veritatis et quasi architecto beatae vitae dicta sunt explicabo.</p>
  </div>
  <div class="abs btn-red read-more about-more">Read More</div>
  <div class="abs about-screen" role="img" aria-label="Desktop monitor showing the website home page"></div>

  <div class="abs services"></div>
  <h2 class="abs section-title services-title">OUR <em>SERVICES</em></h2>
  <div class="abs services-rule"></div>

  <div class="abs card" style="left:98px">
    <svg width="84" height="84" viewBox="0 0 84 84" aria-hidden="true">
      <g fill="none" stroke="#b3141d" stroke-width="4"><circle cx="38" cy="46" r="28"/><ellipse cx="38" cy="46" rx="12" ry="28"/><path d="M10 46h56M14 32h48M14 60h48"/></g>
      <circle cx="64" cy="22" r="16" fill="#222"/><text x="64" y="29" text-anchor="middle" font-family="Roboto,sans-serif" font-weight="700" font-size="20" fill="#fff">$</text>
    </svg>
    <div class="card-title">INVESTMENT BANKING</div>
    <p class="card-text">Nemo enim ipsam voluptatem quia voluptas sit aspernatur aut odit aut fugit sed quia consequuntur magnis.</p>
    <div class="btn-red read-more">Read More</div>
  </div>

  <div class="abs card featured" style="left:448px">
    <svg width="84" height="84" viewBox="0 0 84 84" aria-hidden="true">
      <g fill="#fff"><rect x="20" y="42" width="10" height="34"/><rect x="34" y="50" width="10" height="26"/><rect x="48" y="56" width="10" height="20"/><rect x="62" y="62" width="10" height="14"/></g>
      <path d="M14 14l24 16 10-6 22 20" fill="none" stroke="#fff" stroke-width="4"/><path d="M62 44l10 4-2-11z" fill="#fff"/>
      <text x="10" y="66" font-family="Roboto,sans-serif" font-weight="700" font-size="24" fill="#fff">$</text>
    </svg>
    <div class="card-title">SALES AND TRADING</div>
    <p class="card-text">Nemo enim ipsam voluptatem quia voluptas sit aspernatur aut odit aut fugit sed quia consequuntur magnis.</p>
    <div class="btn-red read-more">Read More</div>
  </div>

  <div class="abs card" style="left:796px">
    <svg width="84" height="84" viewBox="0 0 84 84" aria-hidden="true">
      <rect x="8" y="14" width="56" height="50" rx="4" fill="#b3141d"/>
      <rect x="8" y="14" width="56" height="12" rx="3" fill="#8e0c12"/>
      <rect x="18" y="8" width="5" height="12" fill="#b3141d"/><rect x="48" y="8" width="5" height="12" fill="#b3141d"/>
      <g fill="#fff"><rect x="14" y="32" width="9" height="8"/><rect x="28" y="32" width="9" height="8"/><rect x="42" y="32" width="9" height="8"/><rect x="14" y="46" width="9" height="8"/><rect x="28" y="46" width="9" height="8"/></g>
      <circle cx="62" cy="62" r="17" fill="#222"/><text x="62" y="70" text-anchor="middle" font-family="Roboto,sans-serif" font-weight="700" font-size="22" fill="#fff">$</text>
    </svg>
    <div class="card-title">INVESTMENT PLANING</div>
    <p class="card-text">Nemo enim ipsam voluptatem quia voluptas sit aspernatur aut odit aut fugit sed quia consequuntur magnis.</p>
    <div class="btn-red read-more">Read More</div>
  </div>

  <div class="abs feature-img-one" role="img" aria-label="Monitor with finance dashboard charts and a round stats panel"></div>
  <h3 class="abs feature-head feature-one-head">Accounts Receivable Financing Companies Compete all in One Place</h3>
  <p class="abs copy feature-one-copy">Nemo enim ipsam voluptatem quia voluptas sit aspernatur aut odit aut fugit, sed quia consequuntur magni dolores eos qui ratione voluptatem sequi nesciunt. Neque porro quisquam est, qui dolorem ipsum quia dolor sit amet, consectetur, adipisci velit, sed quia non numquam eius modi tempora incidunt ut labore et dolore magnam aliquam quaerat volup tatem. Ut enim ad minima veniam, quis nostrum.</p>

  <h3 class="abs feature-head feature-two-head">Compare Bids for Immediate Capital</h3>
  <p class="abs copy feature-two-copy">Nemo enim ipsam voluptatem quia voluptas sit aspernatur aut odit aut fugit, sed quia consequuntur magni dolores eos qui ratione voluptatem sequi nesciunt. Neque porro quisquam est, qui dolorem ipsum quia dolor sit amet, consectetur.</p>
  <ul class="abs checks">
    <li><svg width="20" height="20" viewBox="0 0 20 20" aria-hidden="true"><rect x="1" y="3" width="15" height="15" fill="none" stroke="#222" stroke-width="2"/><path d="M5 10l4 4 9-11" fill="none" stroke="#222" stroke-width="2.6"/></svg>Lorem ipsum dolor sit amet, consectetur adipiscing elit</li>
    <li><svg width="20" height="20" viewBox="0 0 20 20" aria-hidden="true"><rect x="1" y="3" width="15" height="15" fill="none" stroke="#222" stroke-width="2"/><path d="M5 10l4 4 9-11" fill="none" stroke="#222" stroke-width="2.6"/></svg>Sed ut perspiciatis unde omnis iste natus error sit voluptatem</li>
    <li><svg width="20" height="20" viewBox="0 0 20 20" aria-hidden="true"><rect x="1" y="3" width="15" height="15" fill="none" stroke="#222" stroke-width="2"/><path d="M5 10l4 4 9-11" fill="none" stroke="#222" stroke-width="2.6"/></svg>Nemo enim ipsam voluptatem quia voluptas sit</li>
    <li><svg width="20" height="20" viewBox="0 0 20 20" aria-hidden="true"><rect x="1" y="3" width="15" height="15" fill="none" stroke="#222" stroke-width="2"/><path d="M5 10l4 4 9-11" fill="none" stroke="#222" stroke-width="2.6"/></svg>Qui dolorem ipsum quia dolor sit amet, consectetur, adipiscin</li>
  </ul>
  <div class="abs feature-img-two" role="img" aria-label="Laptop with charts, calculator and 3D bar and pie graphs"></div>

  <div class="abs cta" role="img" aria-label="Darkened photo of a smiling woman at work"></div>
  <h2 class="abs cta-title">SIGNING UP TAKES JUST A FEW SHORT MINUTES</h2>
  <div class="abs cta-btn">Get Started Today</div>

  <div class="abs partners"></div>
  <div class="abs partner" style="left:100px"><i></i></div>
  <div class="abs partner" style="left:274px"><i></i></div>
  <div class="abs partner" style="left:448px"><i></i></div>
  <div class="abs partner" style="left:622px"><i></i></div>
  <div class="abs partner" style="left:796px"><i></i></div>
  <div class="abs partner" style="left:970px"><i></i></div>

  <div class="abs footer"></div>
  <div class="abs brand brand-footer">Merrow Trade Finance</div>
  <div class="abs social" aria-label="Social links"><span></span><span></span><span></span><span></span><span></span></div>

  <div class="abs foot-title" style="left:376px;top:2644px">QUICK LINKS</div>
  <div class="abs foot-rule" style="left:376px;top:2672px"></div>
  <ul class="abs quick-links">
    <li>› Home</li><li>› About Us</li><li>› Services</li><li>› Introducers</li><li>› Blog</li><li>› Contact Us</li>
  </ul>

  <div class="abs foot-title" style="left:526px;top:2644px">CONTACT US</div>
  <div class="abs foot-rule" style="left:526px;top:2672px"></div>
  <div class="abs contact-list">
    <div class="contact-row"><span class="ic"><svg width="16" height="18" viewBox="0 0 16 18" aria-hidden="true"><path d="M8 1a6 6 0 0 0-6 6c0 4.5 6 10 6 10s6-5.5 6-10a6 6 0 0 0-6-6z" fill="#fff"/><circle cx="8" cy="7" r="2.2" fill="#b3141d"/></svg></span><span><b>MERROW TRADE FINANCE,</b><br>14 Calder Row,<br>Leeds LS1 4XY</span></div>
    <div class="contact-row"><span class="ic"><svg width="12" height="18" viewBox="0 0 12 18" aria-hidden="true"><rect x="1" y="1" width="10" height="16" rx="2" fill="none" stroke="#fff" stroke-width="1.8"/><circle cx="6" cy="14" r="1" fill="#fff"/></svg></span><span><b>PHONE:</b><br>0113 496 0582</span></div>
    <div class="contact-row"><span class="ic"><svg width="16" height="12" viewBox="0 0 16 12" aria-hidden="true"><rect x="0" y="0" width="16" height="12" rx="1" fill="#fff"/><path d="M0 0l8 7 8-7" fill="none" stroke="#b3141d" stroke-width="1.5"/></svg></span><span><b>Mail:</b><br>info@merrowtradefinance.example</span></div>
  </div>

  <div class="abs foot-title" style="left:812px;top:2644px">CONTACT FORM</div>
  <div class="abs foot-rule" style="left:812px;top:2672px"></div>
  <div class="abs foot-field" style="left:812px;top:2698px;width:140px;height:36px">Name</div>
  <div class="abs foot-field" style="left:960px;top:2698px;width:140px;height:36px">Phone</div>
  <div class="abs foot-field" style="left:812px;top:2742px;width:288px;height:64px">Message</div>
  <div class="abs send-btn">SEND MESSAGE</div>

  <div class="abs bottom-bar">Copyright © 2016 Merrow Trade finance. All Right Reserved</div>
</div>
</body>
</html>
```